Envelope Design - Winner can do follow-up business

- Varnoko.com is a Swiss-based online store selling business shirts and accessories for business men
- Please visit the webpage to make yourself familiar with the company. Although the text is in German, with Plimbo translator you should be able to understand the main content.
- Our clients are mainly business men between 30 and 60 years old. Mostly with a high income working in the service industry (banking, insurance, lawyers, etc.). Sometimes there wives purchase the shirts for them ;-)
- The colors and the logo are given, as they are also used for the print materials (please see files in attachment)
- I am running several businesses and often need a talented web designer --> the winner gets substantial follow-up business
your task:
-for our company we need a new envelope design
-It should be simple and modern
-please use one of the logos in the followings.
-suprise me :)

```html
<!DOCTYPE html>
<html lang="de">
<head>
<meta charset="utf-8">
<title>Varnoko – Envelope</title>
<link rel="stylesheet" href="https://fonts.googleapis.com/css2?family=Montserrat:wght@500;600&display=swap">
<style>
  :root {
    --backdrop: #3a3a3b;
    --paper: #ffffff;
    --tone-dark: #666668;
    --tone-mid: #a9aaac;
    --tone-light: #e3e4e5;
    --tone-pale: #f6f7f7;
    --gold: #e3cf5e;
    --text-light: #ffffff;
  }
  html, body {
    margin: 0;
    padding: 0;
    width: 1200px;
    height: 900px;
    overflow: hidden;
    background: var(--backdrop);
  }
  .canvas {
    position: relative;
    width: 1200px;
    height: 900px;
  }
  .envelope {
    position: absolute;
    left: 142px;
    top: 221px;
    width: 915px;
    height: 457px;
    background: var(--paper);
    overflow: hidden;
    font-family: "Montserrat", sans-serif;
  }
  .envelope__texture {
    position: absolute;
    inset: 0;
    background:
      linear-gradient(160deg, rgba(0,0,0,0.10) 0%, rgba(0,0,0,0) 45%),
      linear-gradient(100deg,
        var(--tone-dark) 0%,
        #7d7e80 18%,
        var(--tone-mid) 33%,
        var(--tone-light) 48%,
        #eeeff0 62%,
        var(--tone-pale) 78%,
        var(--paper) 100%);
  }
  .sender {
    position: absolute;
    left: 187px;
    top: 40px;
    transform: translateX(-50%);
    display: flex;
    flex-direction: column;
    align-items: center;
    text-align: center;
    white-space: nowrap;
  }
  .brand__mark {
    width: 40px;
    height: 40px;
    background: var(--gold);
  }
  .brand__name {
    margin: 22px 0 0;
    font-size: 44px;
    font-weight: 600;
    letter-spacing: 3px;
    line-height: 1;
    color: var(--gold);
  }
  .sender__address {
    margin: 28px 0 0;
    font-style: normal;
    font-size: 14.5px;
    font-weight: 600;
    line-height: 18px;
    color: var(--text-light);
  }
  .sender__web {
    margin: 18px 0 0;
    font-size: 14.5px;
    font-weight: 600;
    color: var(--text-light);
  }
</style>
</head>
<body>
  <main class="canvas">
    <section class="envelope">
      <div class="envelope__texture" role="img" aria-label="Low-poly faceted background fading from dark grey on the left to white on the right"></div>
      <div class="sender">
        <div class="brand__mark" aria-hidden="true"></div>
        <p class="brand__name">VARNOKO</p>
        <address class="sender__address">
          Varnoko GmbH | Seeblickweg 9<br>
          8715 Orlingen
        </address>
        <p class="sender__web">www.varnoko.com</p>
      </div>
    </section>
  </main>
</body>
</html>
```